FinTech company looking to revamp and expand client-facing interface for our financial models

Pellworth Engines currently has a very simple website that allows clients to interact with our financial models. We are looking to completely redesign the current site and add several extra pages to provide extra functionality. We want the design to have a modern, slick feel, that will work on both a desktop or a tablet. It should be straightforward for clients to move between different pages at any time, and clear from the layout how to interact with the more advanced features. We have included screenshots of existing pages in the attached design brief, as well as sketches of the functionality required by the new pages, but can't provide a direct link to the current site.
Target Market(s)
Professional investors that will be paying to access the interface
Industry/Entity Type
Finance
Number of Pages Required
4 page
Colors
Designer to choose colors to be used in the design.
Look and feel
Each slider illustrates characteristics of the customer's brand and the style your logo design should communicate.

```html
<!DOCTYPE html>
<html lang="en">
<head>
<meta charset="utf-8">
<title>Norva · Portfolio Builder</title>
<link href="https://fonts.googleapis.com/css2?family=Montserrat:wght@500;600;700;800&family=Roboto+Condensed:wght@400&family=Open+Sans:wght@400&display=swap" rel="stylesheet">
<style>
  :root{
    --frame:#e4e4e4;
    --page-top:#e9e9e9;
    --page-bottom:#f7f7f7;
    --white:#ffffff;
    --ink:#111111;
    --dark:#1b1b1b;
    --navy:#0b2f66;
    --teal:#01676a;
    --green:#0aa00a;
    --red:#c40c0c;
    --row-alt:#f1f1f1;
    --divider:#e3e3e3;
    --muted:#666666;
  }
  *{box-sizing:border-box;margin:0;padding:0}
  html,body{width:1200px;height:1011px;overflow:hidden}
  body{background:var(--frame);font-family:"Montserrat",sans-serif;color:var(--ink);position:relative}
  .page{position:absolute;left:14px;top:14px;width:1172px;height:983px;
    background:linear-gradient(var(--page-top),var(--page-bottom) 45%,var(--page-bottom))}
  .topnav{position:absolute;left:0;top:0;width:1172px;height:55px;background:var(--white);
    display:flex;box-shadow:0 3px 8px rgba(0,0,0,.06)}
  .topnav .cell{height:55px;display:flex;align-items:center;justify-content:center;
    border-right:1px solid var(--divider);font-weight:700;font-size:13px;gap:7px}
  .brand{width:166px;font-size:17px;font-weight:800;letter-spacing:.3px}
  .tab{width:83px}
  .spacer{flex:1}
  .topnav .nav-link{font-size:12.5px;font-weight:700}
  .nav-link svg{width:22px;height:22px}
  .models{width:130px;border-left:1px solid var(--divider)}
  .sens{width:164px}
  .fav{width:181px;border-right:none!important}

  .title-btn{position:absolute;left:436px;top:92px;width:300px;height:51px;background:var(--navy);
    color:var(--white);border-radius:3px;display:flex;align-items:center;justify-content:center;
    font-size:19px;font-weight:600;letter-spacing:.4px}

  .members{position:absolute;left:51px;top:161px;width:1070px;height:259px;background:var(--white);
    border-radius:5px;overflow:hidden;box-shadow:0 2px 8px rgba(0,0,0,.05)}
  .row{display:flex;height:64.5px}
  .row.head{height:65px}
  .row .c{display:flex;align-items:center;justify-content:center;height:100%}
  .c1{width:240px;border-right:1px solid var(--divider)}
  .c2{width:240px;border-right:1px solid var(--divider)}
  .c3{flex:1;position:relative}
  .head .c{color:var(--white);font-size:16px;font-weight:600;border-right:1px solid #444}
  .head .c1,.head .c2{background:var(--dark)}
  .head .c3{background:var(--teal);border:none}
  .row.alt{background:var(--row-alt)}
  .body .c{font-family:"Roboto Condensed",sans-serif;font-size:17px}
  .body .c1{justify-content:flex-start;padding-left:23px;gap:44px}
  .remove{width:25px;height:25px}
  .track{position:absolute;top:18px;width:212px;height:28px;border-radius:14px;background:linear-gradient(#ffffff,#e9e9e9);
    border:1px solid #c9c9c9;box-shadow:inset 0 1px 2px rgba(0,0,0,.1)}
  .fill{position:absolute;top:-1px;height:28px;border-radius:14px}
  .fill.neg{background:linear-gradient(#e01010,#b00b0b 60%,#d21a1a)}
  .fill.pos{background:linear-gradient(#12b012,#0a8f0a 60%,#15a815)}

  .action{position:absolute;top:434px;height:37px;border-radius:3px;color:var(--white);
    display:flex;align-items:center;justify-content:center;gap:12px;font-size:13px;font-weight:700}
  .add{left:51px;width:180px;background:var(--navy)}
  .save{left:240px;width:184px;background:var(--green)}

  .collection{position:absolute;left:51px;top:517px;width:1070px;height:392px;background:var(--white);
    border-radius:5px;overflow:hidden;box-shadow:0 2px 8px rgba(0,0,0,.05)}
  .collection .head-bar{height:65px;background:var(--dark);color:var(--white);font-size:16px;font-weight:600;
    display:flex;align-items:center;justify-content:center}
  .chart{position:absolute;left:0;top:65px;width:1070px;height:327px}
  .chart text{font-family:"Open Sans",sans-serif;font-size:11px;fill:var(--muted)}
  .chart .legend-title{font-family:"Times New Roman",serif;font-size:11px;fill:#444}
</style>
</head>
<body>
<div class="page">
  <nav class="topnav">
    <div class="cell brand">NORVA</div>
    <div class="cell tab">250D</div>
    <div class="cell tab">83D</div>
    <div class="cell tab">42D</div>
    <div class="spacer"></div>
    <div class="cell nav-link models">
      <svg viewBox="0 0 24 24" fill="none" stroke="#111" stroke-width="2"><path d="M3 12 12 4l9 8"/><path d="M6 10v10h4v-6h4v6h4V10"/><path d="M16 6V4h2v4"/></svg>
      MODELS</div>
    <div class="cell nav-link sens">
      <svg viewBox="0 0 24 24" fill="#222"><g><circle cx="12" cy="3" r="1.3"/><circle cx="12" cy="21" r="1.3"/><circle cx="3" cy="12" r="1.3"/><circle cx="21" cy="12" r="1.3"/><circle cx="5.6" cy="5.6" r="1.3"/><circle cx="18.4" cy="18.4" r="1.3"/><circle cx="5.6" cy="18.4" r="1.3"/><circle cx="18.4" cy="5.6" r="1.3"/><circle cx="12" cy="7" r="1.1"/><circle cx="12" cy="17" r="1.1"/><circle cx="7" cy="12" r="1.1"/><circle cx="17" cy="12" r="1.1"/><circle cx="12" cy="12" r="1.6"/></g></svg>
      SENSITIVITIES</div>
    <div class="cell nav-link fav">
      <svg viewBox="0 0 24 24" fill="none" stroke="#111" stroke-width="1.8" stroke-linejoin="round"><path d="M12 2.5l2.9 6.2 6.6.7-5 4.6 1.4 6.6L12 17.3l-5.9 3.3 1.4-6.6-5-4.6 6.6-.7z"/></svg>
      FAVOURITES</div>
  </nav>

  <div class="title-btn">PORTFOLIO BUILDER</div>

  <section class="members">
    <div class="row head"><div class="c c1">Members Name</div><div class="c c2">Size</div><div class="c c3">Sensitivities</div></div>
    <div class="row body">
      <div class="c c1"><svg class="remove" viewBox="0 0 26 26" fill="none" stroke="#b01818" stroke-width="2"><circle cx="13" cy="13" r="11"/><path d="M7.5 13h11"/></svg>Member 1</div>
      <div class="c c2">0.2</div>
      <div class="c c3"><div class="track" style="left:83px"><div class="fill neg" style="left:92px;width:120px"></div></div></div>
    </div>
    <div class="row body alt">
      <div class="c c1"><svg class="remove" viewBox="0 0 26 26" fill="none" stroke="#b01818" stroke-width="2"><circle cx="13" cy="13" r="11"/><path d="M7.5 13h11"/></svg>Member 2</div>
      <div class="c c2">0.5</div>
      <div class="c c3"><div class="track" style="left:295px"><div class="fill pos" style="left:-1px;width:120px"></div></div></div>
    </div>
    <div class="row body">
      <div class="c c1"><svg class="remove" viewBox="0 0 26 26" fill="none" stroke="#b01818" stroke-width="2"><circle cx="13" cy="13" r="11"/><path d="M7.5 13h11"/></svg>Member 3</div>
      <div class="c c2">-0.3</div>
      <div class="c c3"><div class="track" style="left:295px"><div class="fill pos" style="left:-1px;width:157px"></div></div></div>
    </div>
  </section>

  <div class="action add">
    <svg width="22" height="22" viewBox="0 0 22 22" fill="none" stroke="#fff" stroke-width="1.6"><circle cx="11" cy="11" r="9.5"/><path d="M11 6v10M6 11h10"/></svg>
    ADD A MEMBER</div>
  <div class="action save">
    <svg width="24" height="20" viewBox="0 0 24 20" fill="none" stroke="#fff" stroke-width="3.4" stroke-linecap="round" stroke-linejoin="round"><path d="M3 10l6 6L21 3"/></svg>
    SAVE PORTFOLIO</div>

  <section class="collection">
    <div class="head-bar">Properties of Collection</div>
    <svg class="chart" viewBox="51 582 1070 327" width="1070" height="327">
      <g stroke="#ececec" stroke-width="1">
        <line x1="163" y1="650" x2="163" y2="840"/><line x1="296" y1="650" x2="296" y2="840"/>
        <line x1="427" y1="650" x2="427" y2="840"/><line x1="557" y1="650" x2="557" y2="840"/>
        <line x1="684" y1="650" x2="684" y2="840"/><line x1="815" y1="650" x2="815" y2="840"/>
        <line x1="946" y1="650" x2="946" y2="840"/>
        <line x1="137" y1="665" x2="995" y2="665"/><line x1="137" y1="697" x2="995" y2="697"/>
        <line x1="137" y1="729" x2="995" y2="729"/><line x1="137" y1="795" x2="995" y2="795"/>
        <line x1="137" y1="827" x2="995" y2="827"/>
      </g>
      <line x1="137" y1="762" x2="995" y2="762" stroke="#999" stroke-width="1.5"/>
      <g text-anchor="end">
        <text x="133" y="669">6</text><text x="133" y="701">4</text><text x="133" y="733">2</text>
        <text x="133" y="766">0</text><text x="133" y="799">−2</text><text x="133" y="831">−4</text>
      </g>
      <g text-anchor="middle">
        <text x="163" y="858">Jul 2018</text><text x="296" y="858">Sep 2018</text><text x="427" y="858">Nov 2018</text>
        <text x="557" y="858">Jan 2019</text><text x="684" y="858">Mar 2019</text><text x="815" y="858">May 2019</text>
        <text x="946" y="858">Jul 2019</text>
      </g>
      <g fill="none" stroke="#1a1a1a" stroke-width="16" stroke-dasharray="1.3 3.2">
        <polyline points="180,710 200,705 230,702 260,705 290,700 320,705 350,703 370,684 385,702 410,713 440,715 470,713 500,700 530,707 560,710 590,707 610,689 640,684 660,682 700,680 740,682 770,689 800,694 840,700 880,707 905,718 930,720 950,716"/>
        <polyline points="180,803 220,801 270,798 320,798 385,799 400,808 430,811 460,806 500,808 530,814 560,816 600,813 625,809 640,819 680,824 720,827 760,822 800,821 830,824 860,819 900,821 950,822"/>
      </g>
      <g fill="none" stroke-width="6" stroke-linecap="round" stroke-dasharray="0 5.5">
        <polyline stroke="#b9b93a" points="180,710 200,705 230,702 260,705 290,700 320,705 350,703 370,684 385,702 410,713 440,715 470,713 500,700 530,707 560,710 590,707 610,689 640,684 660,682 700,680 740,682 770,689 800,694 840,700 880,707 905,718 930,720 950,716"/>
        <polyline stroke="#3b6fb3" points="180,803 220,801 270,798 320,798 385,799 400,808 430,811 460,806 500,808 530,814 560,816 600,813 625,809 640,819 680,824 720,827 760,822 800,821 830,824 860,819 900,821 950,822"/>
      </g>
      <g stroke="#1a1a1a" stroke-width="1.3"><line x1="924" y1="777" x2="924" y2="793"/><line x1="932" y1="777" x2="932" y2="793"/></g>
      <g fill="#3a9a3a"><circle cx="924" cy="785" r="3"/><circle cx="932" cy="785" r="3"/></g>
      <text class="legend-title" x="1045" y="667">Names</text>
      <g>
        <circle cx="1030" cy="665" r="3" fill="#8fb8de"/><circle cx="1030" cy="682" r="3" fill="#f4b27a"/>
        <circle cx="1030" cy="699" r="3" fill="#3a9a3a"/><circle cx="1030" cy="716" r="3" fill="#e07b7b"/>
        <circle cx="1030" cy="733" r="3" fill="#b8a0d4"/><circle cx="1030" cy="750" r="3" fill="#b09a8f"/>
        <circle cx="1030" cy="767" r="3" fill="#f0b6dc"/><circle cx="1030" cy="784" r="3" fill="#bdbdbd"/>
        <circle cx="1030" cy="801" r="3" fill="#b9b93a"/><circle cx="1030" cy="818" r="3" fill="#8fdcdc"/>
        <circle cx="1030" cy="835" r="3" fill="#3b6fb3"/>
      </g>
    </svg>
  </section>
</div>
</body>
</html>
```